Halvery Construction Group Website

Need a dynamic corporate website that can be built on with time. We want to get our information out to the world and have a place where customers can submit requests for proposals.

Target Market(s)

Custom home owners and buyers. Architects and Real Estate Agents.

Industry/Entity Type

Construction

Number of Pages Required

3 page

Font styles to use
Serif
Sans Serif

Requirements
Must have
• Company logo, about, company contact information, biography, contact, projects,
• Sleek, modern, clean, attractive design.
• Online form customers can use for filling out a request for project proposal.
• Linkedin hyperlink.
• Uses www.halveryconstructiongroup.example

```html
<!DOCTYPE html>
<html lang="en">
<head>
<meta charset="utf-8">
<title>Halvery Construction Group</title>
<link rel="stylesheet" href="https://fonts.googleapis.com/css2?family=Roboto+Condensed:wght@400;700&family=Open+Sans:wght@400;700&display=swap">
<style>
:root{
  --blue:#0a51a0;
  --blue-dark:#084a93;
  --sky:#2f9fd8;
  --input:#2f9fd8;
  --grey-bar:#f3f3f3;
  --grey-section:#efefef;
  --text:#555;
  --muted:#707070;
  --white:#fff;
}
*{box-sizing:border-box;margin:0;padding:0}
html,body{width:682px;height:1200px;overflow:hidden;background:#fff}
body{position:relative;font-family:"Open Sans",sans-serif;color:var(--text)}
.cond{font-family:"Roboto Condensed",sans-serif}
.abs{position:absolute}
.topbar{left:0;top:0;width:682px;height:24px;background:var(--grey-bar);border-bottom:1px solid #e2e2e2}
.topbar .social{left:44px;top:6px;display:flex;align-items:center;gap:5px;font-size:10px;color:var(--blue)}
.dot{display:inline-block;width:10px;height:10px;background:var(--blue);border-radius:2px}
.topbar .phone{right:46px;top:3px;display:flex;align-items:center;gap:5px;font-family:"Roboto Condensed",sans-serif;font-weight:700;font-size:15px;color:var(--blue)}
.brand{left:44px;top:38px;display:flex;align-items:center;gap:8px}
.brand .mark{width:40px;height:40px;background:var(--blue);border-radius:4px}
.brand .name{font-family:"Roboto Condensed",sans-serif;font-size:24px;font-weight:700;color:var(--blue);line-height:1}
.brand .sub{font-family:"Roboto Condensed",sans-serif;font-size:9px;color:#666;letter-spacing:.2px}
.nav{left:335px;top:39px;display:flex;align-items:center;font-family:"Roboto Condensed",sans-serif;font-size:12.5px;color:#777}
.nav a{color:inherit;text-decoration:none;padding:0 11px;line-height:29px}
.nav a.active{background:var(--blue);color:#fff;border-radius:2px;padding:0 13px}
.hero{left:0;top:89px;width:682px;height:324px;background:linear-gradient(90deg,#e9ecef 0%,#f7f8f9 25%,#cfd6dc 55%,#e7ebee 80%,#c4ccd3 100%)}
.band{left:0;top:413px;width:682px;height:71px;background:var(--blue)}
.band h2{position:absolute;left:46px;top:19px;font-family:"Roboto Condensed",sans-serif;font-weight:400;font-size:23px;color:#fff}
.band .btn{position:absolute;left:524px;top:17px;width:114px;height:32px;background:#fff;border-radius:2px;color:var(--blue);font-family:"Roboto Condensed",sans-serif;font-size:13.5px;display:flex;align-items:center;justify-content:center;gap:4px}
.welcome{left:0;top:505px;width:682px;text-align:center}
.welcome .pre{font-family:"Roboto Condensed",sans-serif;font-size:14px;color:var(--muted)}
.welcome h1{font-family:"Roboto Condensed",sans-serif;font-weight:400;font-size:24px;color:var(--blue);margin-top:1px}
.welcome p{width:520px;margin:7px auto 0;font-size:8.6px;line-height:14.4px;color:var(--text)}
.service{top:616px;display:flex;gap:10px}
.service .img{width:118px;height:80px}
.service h3{font-family:"Roboto Condensed",sans-serif;font-weight:400;font-size:15px;color:var(--blue);line-height:1;margin-top:1px}
.service p{width:160px;font-size:8.6px;line-height:14.4px;margin-top:3px}
.more{font-size:8.6px;font-weight:700;color:var(--blue);margin-top:4px}
.projects{left:0;top:733px;width:682px;height:289px;background:var(--grey-section)}
.projects h2{position:absolute;width:100%;top:29px;text-align:center;font-family:"Roboto Condensed",sans-serif;font-weight:400;font-size:24px;color:var(--muted)}
.projects h2 span{color:var(--blue)}
.proj{position:absolute;top:66px;width:133px}
.proj .img{height:80px}
.proj h4{font-weight:400;font-size:9.6px;color:var(--blue);margin:7px 0 0 2px}
.proj p{font-size:8.6px;line-height:14.4px;margin:3px 0 0 2px}
.viewall{position:absolute;left:302px;top:228px;width:77px;height:26px;background:var(--blue);border-radius:2px;color:#fff;font-family:"Roboto Condensed",sans-serif;font-size:13px;display:flex;align-items:center;justify-content:center}
.footer{left:0;top:1022px;width:682px;height:149px;background:var(--blue);color:#fff}
.fcol{position:absolute;top:20px}
.fcol h5{font-family:"Roboto Condensed",sans-serif;font-weight:400;font-size:15px;margin-bottom:6px}
.fcol p,.fcol li{font-size:8.6px;line-height:14.4px}
.fbrand{font-family:"Roboto Condensed",sans-serif;font-size:19px;font-weight:700;display:flex;align-items:center;gap:6px}
.fbrand .mark{width:20px;height:20px;background:#fff;border-radius:3px;opacity:.85}
.fcol ul{list-style:none}
.fcol ul li{font-size:10px;line-height:18px;display:flex;align-items:center;gap:5px}
.ficon{display:flex;gap:5px;align-items:flex-start;margin-bottom:7px}
.ficon svg{flex:none;margin-top:2px}
.email{width:133px;height:20px;background:var(--input);color:#eaf6fd;font-size:8.6px;padding:4px 5px;margin-top:7px}
.subscribe{width:80px;height:23px;background:#fff;color:var(--blue);font-family:"Roboto Condensed",sans-serif;font-size:12px;display:flex;align-items:center;justify-content:center;margin-top:6px;border-radius:1px}
.circle{width:26px;height:26px;border-radius:50%;background:#fff}
.copy{left:0;top:1171px;width:682px;height:29px;background:var(--sky);color:#fff;font-size:8.2px;text-align:center;line-height:29px}
</style>
</head>
<body>
<div class="abs topbar">
  <div class="abs social"><span class="dot"></span>Network</div>
  <div class="abs phone">
    <svg width="13" height="13" viewBox="0 0 24 24"><path fill="currentColor" d="M6.6 10.8a15 15 0 0 0 6.6 6.6l2.2-2.2c.3-.3.7-.4 1-.2 1.1.4 2.3.6 3.6.6.6 0 1 .4 1 1V20c0 .6-.4 1-1 1A17 17 0 0 1 3 4c0-.6.4-1 1-1h3.5c.6 0 1 .4 1 1 0 1.3.2 2.5.6 3.6.1.3 0 .7-.2 1z"/></svg>
    123 555 0190
  </div>
</div>

<div class="abs brand">
  <span class="mark"></span>
  <div><div class="name">HALVERY</div><div class="sub">CONSTRUCTION GROUP, INC.</div></div>
</div>
<nav class="abs nav">
  <a class="active" href="#">HOME</a><a href="#">ABOUT</a><a href="#">PROJECTS</a><a href="#">NEWS</a><a href="#">CONTACT</a>
</nav>

<div class="abs hero" role="img" aria-label="Bright modern office interior with glass partitions, white sculpted wall and a yellow lounge chair"></div>

<div class="abs band">
  <h2>LOREM IPSUM IS SUMMY TEXT AND PRINTING.</h2>
  <div class="btn">CONTACT US
    <svg width="12" height="12" viewBox="0 0 24 24"><path fill="currentColor" d="M12 3l-2.4 2.4 4.9 4.9H3v3.4h11.5l-4.9 4.9L12 21l9-9z"/></svg>
  </div>
</div>

<section class="abs welcome">
  <div class="pre">WELCOME TO</div>
  <h1>HALVERY CONSTRUCTION GROUP, INC.</h1>
  <p>Lorem Ipsum is simply dummy text of the printing and typesetting industry. Lorem Ipsum has been the industry's standard dummy text ever since the 1500s, when an unknown printer took a galley of type and scrambled it to make a type specimen book, It has survived not only five centuries.</p>
</section>

<div class="abs service" style="left:44px">
  <div class="img" role="img" aria-label="Glass office towers seen from below" style="background:linear-gradient(135deg,#dfe8f0,#7d9bb6 60%,#3d5d7a)"></div>
  <div><h3>Commercial</h3><p>Lorem Ipsum is simply dummy text of the printing and typesetting industry. Lorem Ipsum has been the industry.</p><div class="more">READ MORE »</div></div>
</div>
<div class="abs service" style="left:353px">
  <div class="img" role="img" aria-label="Lit family house at dusk with front lawn" style="background:linear-gradient(180deg,#7f9ccd 0%,#b9b4a8 55%,#4f7a2f 100%)"></div>
  <div><h3>Residential</h3><p>Lorem Ipsum is simply dummy text of the printing and typesetting industry. Lorem Ipsum has been the industry.</p><div class="more">READ MORE »</div></div>
</div>

<section class="abs projects">
  <h2>LATEST <span>PROJECT</span></h2>
  <div class="proj" style="left:44px"><div class="img" role="img" aria-label="Modern office interior with glass walls" style="background:linear-gradient(90deg,#eef0f2,#c6ced5 60%,#9fabb6)"></div><h4>Lorem Ipsum is dummy text.</h4><p>Lorem Ipsum is simply dummy text of the printing and type setting industry.</p></div>
  <div class="proj" style="left:198px"><div class="img" role="img" aria-label="Suburban houses on a tree-lined street" style="background:linear-gradient(180deg,#5d93d4 0%,#a9b7c4 50%,#5d8a34 100%)"></div><h4>Lorem Ipsum is dummy text.</h4><p>Lorem Ipsum is simply dummy text of the printing and type setting industry.</p></div>
  <div class="proj" style="left:351px"><div class="img" role="img" aria-label="Bright living and dining room with chandelier" style="background:linear-gradient(90deg,#d9d3c8,#f3f1ec 50%,#cfc8bb)"></div><h4>Lorem Ipsum is dummy text.</h4><p>Lorem Ipsum is simply dummy text of the printing and type setting industry.</p></div>
  <div class="proj" style="left:505px"><div class="img" role="img" aria-label="Tower under construction with yellow cranes" style="background:linear-gradient(160deg,#2e6fc0 0%,#8fb6e2 50%,#6c6a5e 100%)"></div><h4>Lorem Ipsum is dummy text.</h4><p>Lorem Ipsum is simply dummy text of the printing and type setting industry.</p></div>
  <div class="viewall">VIEW ALL</div>
</section>

<footer class="abs footer">
  <div class="fcol" style="left:44px;width:135px">
    <div class="fbrand"><span class="mark"></span>HALVERY</div>
    <p style="margin-top:10px">Lorem Ipsum is simply dummy text of the printing and type setting industry.</p>
    <div style="display:flex;align-items:center;gap:8px;margin-top:6px;font-size:10px"><span class="circle"></span>Network</div>
  </div>
  <div class="fcol" style="left:198px">
    <h5>Useful Links</h5>
    <ul><li>› Home</li><li>› About</li><li>› Projects</li><li>› News</li><li>› Contact</li></ul>
  </div>
  <div class="fcol" style="left:351px;width:140px">
    <h5>Get In Touch</h5>
    <div class="ficon"><svg width="9" height="11" viewBox="0 0 24 30"><path fill="#fff" d="M12 0a10 10 0 0 0-10 10c0 7.5 10 20 10 20s10-12.5 10-20A10 10 0 0 0 12 0zm0 14a4 4 0 1 1 0-8 4 4 0 0 1 0 8z"/></svg><p>Lorem Ipsum is dummy text of the printing.</p></div>
    <div class="ficon" style="font-weight:700;font-size:8.6px"><svg width="11" height="11" viewBox="0 0 24 24"><path fill="#fff" d="M6.6 10.8a15 15 0 0 0 6.6 6.6l2.2-2.2c.3-.3.7-.4 1-.2 1.1.4 2.3.6 3.6.6.6 0 1 .4 1 1V20c0 .6-.4 1-1 1A17 17 0 0 1 3 4c0-.6.4-1 1-1h3.5c.6 0 1 .4 1 1 0 1.3.2 2.5.6 3.6.1.3 0 .7-.2 1z"/></svg>123 555 0190</div>
    <div class="ficon"><svg width="11" height="9" viewBox="0 0 24 18"><rect x="1" y="1" width="22" height="16" fill="none" stroke="#fff" stroke-width="2"/><path d="M1 1l11 9 11-9" fill="none" stroke="#fff" stroke-width="2"/></svg><p style="word-break:break-all">info@halveryconstructiongroup.example</p></div>
  </div>
  <div class="fcol" style="left:505px;width:135px">
    <h5>Newsletter</h5>
    <p>Subscribe to stay on HALVERY CONSTRUCTION GROUP, INC.</p>
    <div class="email">Enter Email Id</div>
    <div class="subscribe">SUBSCRIBE</div>
  </div>
</footer>
<div class="abs copy">© <b>HALVERY CONSTRUCTION GROUP, INC.</b> - 2016. All Rights Reserved.</div>
</body>
</html>
```